The Brandwell Firm

We need a new design for our letterhead and envelopes. We are a personal injury and criminal defense firm so we need something modern and clean, but more on the professional/traditional side. Our new logo has two colors and is attached to the file so we need something that works well with those colors/matches the design. The following information needs to be on the letterhead:
Phone: (555) 214-3370
Fax: (555) 214-5186
Toll-Free: (888) 431-2059
Post Office Box 4721
Millbrook, SC 29555-4721
HarmClaimCounsel.example
PalmettoTrialAdvocates.example

Target Market(s)

Clients, government agencies, other law firms

Industry/Entity Type

Legal

Font styles to use
Sans Serif
Other font styles liked:
• Arial

Colors

Designer to choose colors to be used in the design.

Requirements
Must have
• Must look professional and clean, modern
Nice to have
• I would like to see a design that works with the logo but does not distract from the content that will be printed on it
Should not have
• Too many colors or crazy designs.

```html
<!DOCTYPE html>
<html lang="en">
<head>
<meta charset="utf-8">
<title>The Brandwell Firm – Stationery</title>
<link rel="stylesheet" href="https://fonts.googleapis.com/css2?family=Roboto:wght@400;500&family=Questrial&display=swap">
<style>
  :root {
    --bg: #dcdcdc;
    --red: #d21c24;
    --blue: #2d3192;
    --ink: #444;
    --ink-soft: #555;
    --paper-light: #f3f3f3;
    --paper-dark: #dedede;
  }
  * { box-sizing: border-box; margin: 0; padding: 0; }
  html, body { width: 1200px; height: 877px; overflow: hidden; background: var(--bg); }
  .canvas { position: relative; width: 1200px; height: 877px; }

  .paper {
    position: absolute;
    background: linear-gradient(90deg, var(--paper-light) 0%, var(--paper-dark) 100%);
    overflow: hidden;
  }
  .wave { position: absolute; left: 0; bottom: 0; width: 100%; height: 54px; display: block; }
  .wave path { fill: var(--red); }

  .brand { display: flex; align-items: center; gap: 6px; }
  .brand-dot { width: 12px; height: 12px; border-radius: 50%; background: var(--red); flex: none; }
  .brand-name { font-family: "Roboto", sans-serif; font-weight: 500; color: var(--blue); font-size: 15px; white-space: nowrap; }

  /* Letterhead */
  .letterhead { left: 69px; top: 64px; width: 527px; height: 742px; }
  .letterhead .brand { position: absolute; left: 47px; top: 66px; }
  .contact {
    position: absolute; right: 44px; top: 43px; text-align: right;
    font-family: "Roboto", sans-serif; font-size: 7.6px; line-height: 10.4px; color: var(--ink-soft);
  }
  .contact .group + .group { margin-top: 3px; }
  .contact .label { color: var(--red); }
  .letter-body { position: absolute; left: 46px; top: 207px; width: 437px; font-family: "Questrial", sans-serif; color: var(--ink-soft); }
  .salutation { font-size: 13.6px; color: #555; margin-bottom: 22px; }
  .letter-body p.copy { font-size: 7.4px; line-height: 11.4px; text-align: justify; margin-bottom: 11px; }
  .closing { font-size: 7.6px; margin-top: 20px; }
  .signature { display: block; width: 96px; height: 38px; margin-top: 18px; background: linear-gradient(90deg, rgba(45,49,146,.25), rgba(45,49,146,.1)); border-radius: 3px; }

  /* Envelopes */
  .envelope-back { left: 645px; top: 190px; width: 531px; height: 240px; background: linear-gradient(90deg, #ececec, #e2e2e2); }
  .envelope-front { left: 611px; top: 280px; width: 531px; height: 242px; }
  .flap { position: absolute; left: 0; top: 0; width: 100%; height: 74px; display: block; }
  .flap-red path { fill: var(--red); }
  .flap-blue path { fill: var(--blue); }
  .flap-seal { position: absolute; left: 50%; width: 26px; height: 26px; margin-left: -13px; border-radius: 50%; }
  .envelope-back .flap-seal { top: 30px; background: var(--blue); }
  .envelope-front .flap-seal { top: 30px; background: var(--red); }
  .envelope-urls {
    position: absolute; left: 0; right: 0; bottom: 15px; text-align: center;
    font-family: "Roboto", sans-serif; font-size: 7.6px; color: var(--ink-soft); padding-left: 20px;
  }

  .envelope-small { left: 614px; top: 562px; width: 532px; height: 242px; }
  .envelope-small .brand { position: absolute; left: 24px; top: 48px; }
  .return-address { position: absolute; left: 32px; top: 90px; font-family: "Roboto", sans-serif; font-size: 7.6px; line-height: 10px; color: var(--ink-soft); }
</style>
</head>
<body>
<div class="canvas">

  <section class="paper letterhead">
    <div class="brand">
      <span class="brand-dot"></span>
      <span class="brand-name">The Brandwell Firm</span>
    </div>
    <address class="contact" style="font-style:normal">
      <div class="group">Post Office Box 4721<br>Millbrook, SC 29555-4721</div>
      <div class="group">
        <span class="label">(P)</span> (555) 214-3370<br>
        <span class="label">(F)</span> (555) 214-5186<br>
        <span class="label">(TF)</span> (888) 431-2059
      </div>
      <div class="group">HarmClaimCounsel.example<br>PalmettoTrialAdvocates.example</div>
    </address>

    <div class="letter-body">
      <p class="salutation">Dear Mr. Hale,</p>
      <p class="copy">Lorem ipsum dolor sit amet, consectetur adipiscing elit. Donec orci purus, luctus vitae dignissim eu, iaculis sed purus. Vivamus faucibus, ipsum nec aliquet viverra, leo mauris condimentum ligula, sit amet sagittis enim ligula quis arcu. Nam egestas tortor id nisi porttitor mattis. In tortor ante, ultricies in suscipit a, tempus non massa. Vivamus et auctor mi. Fusce vel massa nulla. Phasellus nec eros mauris, et scelerisque orci.</p>
      <p class="copy">Donec malesuada orci vitae nulla accumsan porta a id massa. Quisque accumsan iaculis magna sit amet fringilla. Maecenas consequat, magna eget tincidunt semper, odio nibh rutrum mi, id feugiat ante nisi eu risus. Vestibulum nunc orci, rhoncus a placerat in, ultricies in mi. Cras mattis varius eros, vel fringilla nisi suscipit eget. Quisque scelerisque sagittis nulla at porttitor.</p>
      <p class="copy">Sed id augue vitae urna euismod commodo aliquet a quam. Pellentesque arcu velit, cursus et malesuada ut, consequat et diam. Nullam erat sem, rhoncus id ullamcorper vitae, rhoncus et arcu. In ultricies ultricies nulla, ut rutrum nisi iaculis at. Donec eu magna a metus ornare faucibus. Fusce aliquet faucibus ultricies. Morbi semper, est id tincidunt gravida, sem arcu adipiscing lacus, ac bibendum nulla leo eu purus. Quisque nec diam sed risus consectetur a accumsan quis quis nibh. Vestibulum id purus lorem.</p>
      <p class="copy">It is a long established fact that a reader will be distracted by the readable content of a page when looking at its layout. The point of using Lorem Ipsum is that it has a more-or-less normal distribution of letters, as opposed to using 'Content here, content here', making it look like readable English. Many desktop publishing packages</p>
      <p class="closing">Sincerely,</p>
      <span class="signature" role="img" aria-label="Handwritten signature of the sender"></span>
    </div>

    <svg class="wave" viewBox="0 0 527 54" preserveAspectRatio="none" aria-hidden="true">
      <path d="M0,54 C50,32 160,12 225,36 C190,42 160,50 150,54 Z"/>
      <path d="M170,54 C215,40 255,4 322,2 C385,0 425,46 472,52 C500,55 518,42 527,34 L527,54 Z"/>
    </svg>
  </section>

  <section class="paper envelope-back">
    <svg class="flap flap-red" viewBox="0 0 531 74" preserveAspectRatio="none" aria-hidden="true">
      <path d="M0,0 H531 L518,50 Q512,74 488,74 H43 Q19,74 13,50 Z"/>
    </svg>
    <span class="flap-seal"></span>
  </section>

  <section class="paper envelope-front">
    <svg class="flap flap-blue" viewBox="0 0 531 74" preserveAspectRatio="none" aria-hidden="true">
      <path d="M0,0 H531 L518,50 Q512,74 488,74 H43 Q19,74 13,50 Z"/>
    </svg>
    <span class="flap-seal"></span>
    <p class="envelope-urls">www.HarmClaimCounsel.example | &nbsp;www.PalmettoTrialAdvocates.example</p>
  </section>

  <section class="paper envelope-small">
    <div class="brand">
      <span class="brand-dot"></span>
      <span class="brand-name">The Brandwell Firm</span>
    </div>
    <address class="return-address" style="font-style:normal">Post Office Box 4721<br>Millbrook, SC 29555-4721</address>
    <svg class="wave" viewBox="0 0 527 54" preserveAspectRatio="none" aria-hidden="true">
      <path d="M0,54 C50,32 160,12 225,36 C190,42 160,50 150,54 Z"/>
      <path d="M170,54 C215,40 255,4 322,2 C385,0 425,46 472,52 C500,55 518,42 527,34 L527,54 Z"/>
    </svg>
  </section>

</div>
</body>
</html>
```